CD Cover für junge Pop-Rock Band
Sehr kreative vorschläge. mehrere designs, die alle unter den top-favoriten für uns waren. änderungen und anpassungen stets schnell umgesetzt und auch nach gewinner-auswahl noch weiter zusammen gearbeitet bevor das endgültige design übergeben wurde.
Zielgruppe
Wir sind eine junge Band aus München und machen ausschließlich eigene Songs im Bereich Pop-Rock. Durch Einflüsse aus verschiedenen anderen Genres wie Funk, Reggae und Britpop grenzen sich unsere Songs von typischem Mainstream-Pop ab. Unsere Zielgruppe setzt sich aus Personen verschiedener Altersgruppen zusammen, der Fokus liegt jedoch auf Mitte Zwanzig- bis Mitte Dreißig-Jährigen.
Homepage: www.okapimind.com
Sozialnetz: www.sozialnetz.example/okapimindband
Aufgabenstellung
Wir benötigen ein Design für unsere neue EP "Open Gates". Diese wird in Form eines DigiPacks veröffentlicht werden. Daher werden Designs für Vorderseite, Rückseite, zwei Innenseiten sowie die CD selbst benötigt.
Folgendes sollte auf den jeweiligen Seiten enthalten sein:
Vorderseite:
- Bandschriftzug (siehe Anhang)
- Name der EP: Open Gates
Rückseite:
- Trackliste (1.Velvet Spoon, 2.Hold It Near, 3.Harbor Pike, 4.Can We Stay, 5.Brightest Edge)
- Credits (Recording by ..., Mix by ..., Mastering by ..., etc. -> wird noch festgesetzt)
Anmerkung:
Die roten Kratzer aus dem Bandlogo können bei Bedarf frei verwendet werden hinsichtlich Farbe, Muster, Gestaltung, Größe, etc.
Wir möchten keine Bilder von uns (z.B. von unserer Homepage, Sozialnetz, etc) auf der CD.

```html
<!DOCTYPE html>
<html lang="en">
<head>
<meta charset="utf-8">
<title>OkapiMind – Open Gates – Digipack</title>
<link rel="stylesheet" href="https://fonts.googleapis.com/css2?family=Raleway:wght@300&family=Montserrat:wght@700;800&family=Oswald:wght@500&display=swap">
<style>
  :root{
    --stage:#e4e4e0;
    --paper:#ffffff;
    --ink:#2a2a2e;
    --ink-soft:#6f6f74;
    --mute:#c9c9cc;
    --mark:#c8202a;
    --peach:#f4cdb0;
    --rose:#e56fb0;
    --magenta:#b6338f;
    --violet:#6b3fa8;
    --indigo:#3a2f86;
    --shadow:0 2px 3px rgba(0,0,0,.25);
  }
  *{box-sizing:border-box;margin:0;padding:0}
  html,body{width:1066px;height:1200px;overflow:hidden}
  body{background:var(--stage);position:relative;font-family:"Montserrat",sans-serif}

  .panel{position:absolute;width:340px;height:302px;background:var(--paper);box-shadow:var(--shadow);overflow:hidden}
  .panel--front{left:13px;top:278px}
  .panel--back{left:383px;top:278px}
  .panel--inside-left{left:193px;top:622px}
  .panel--inside-right{left:563px;top:622px}

  .artwork{position:absolute;inset:0}
  .panel--front .artwork{
    background:
      radial-gradient(ellipse 70px 55px at 95px 70px, rgba(244,205,176,.95), transparent 70%),
      radial-gradient(ellipse 55px 45px at 200px 45px, rgba(244,205,176,.9), transparent 70%),
      radial-gradient(ellipse 60px 40px at 70px 125px, rgba(182,51,143,.7), transparent 70%),
      radial-gradient(ellipse 50px 40px at 140px 160px, rgba(107,63,168,.75), transparent 70%),
      radial-gradient(ellipse 55px 45px at 160px 240px, rgba(182,51,143,.85), transparent 70%),
      radial-gradient(ellipse 40px 35px at 260px 235px, rgba(107,63,168,.8), transparent 70%),
      radial-gradient(ellipse 45px 30px at 70px 10px, rgba(58,47,134,.6), transparent 70%),
      radial-gradient(ellipse 40px 40px at 270px 20px, rgba(229,111,176,.6), transparent 70%);
  }
  .panel--back .artwork{
    background:
      radial-gradient(ellipse 55px 60px at 250px 60px, rgba(58,47,134,.75), transparent 70%),
      radial-gradient(ellipse 60px 55px at 270px 150px, rgba(244,205,176,.9), transparent 70%),
      radial-gradient(ellipse 55px 60px at 170px 190px, rgba(107,63,168,.85), transparent 70%),
      radial-gradient(ellipse 40px 45px at 200px 130px, rgba(244,205,176,.85), transparent 70%),
      radial-gradient(ellipse 60px 40px at 180px 285px, rgba(229,111,176,.75), transparent 70%),
      radial-gradient(ellipse 35px 40px at 120px 240px, rgba(182,51,143,.6), transparent 70%);
  }
  .panel--inside-left .artwork{
    background:
      radial-gradient(ellipse 60px 50px at 175px 55px, rgba(244,205,176,.9), transparent 70%),
      radial-gradient(ellipse 40px 50px at 30px 90px, rgba(182,51,143,.8), transparent 70%),
      radial-gradient(ellipse 45px 40px at 255px 45px, rgba(244,205,176,.8), transparent 70%),
      radial-gradient(ellipse 60px 55px at 180px 145px, rgba(107,63,168,.75), transparent 70%),
      radial-gradient(ellipse 70px 55px at 150px 250px, rgba(58,47,134,.8), transparent 70%),
      radial-gradient(ellipse 45px 45px at 60px 250px, rgba(244,205,176,.85), transparent 70%),
      radial-gradient(ellipse 45px 40px at 120px 25px, rgba(229,111,176,.7), transparent 70%);
  }
  .panel--inside-right .artwork{
    background:
      radial-gradient(ellipse 110px 55px at 200px 40px, rgba(244,205,176,.95), transparent 70%),
      radial-gradient(ellipse 70px 55px at 200px 140px, rgba(107,63,168,.8), transparent 70%),
      radial-gradient(ellipse 45px 50px at 200px 210px, rgba(182,51,143,.6), transparent 70%),
      radial-gradient(ellipse 70px 55px at 280px 270px, rgba(182,51,143,.85), transparent 70%),
      radial-gradient(ellipse 30px 40px at 330px 130px, rgba(229,111,176,.6), transparent 70%);
  }

  .brand{position:absolute;display:flex;align-items:center;gap:4px}
  .brand__square{width:9px;height:9px;background:var(--ink)}
  .brand__name{font-family:"Raleway",sans-serif;font-weight:300;color:var(--ink);letter-spacing:-.5px}
  .panel--front .brand{left:170px;top:144px}
  .panel--front .brand__name{font-size:22px}
  .release-title{position:absolute;font-weight:700;color:var(--mute);letter-spacing:1.5px;text-transform:uppercase}
  .panel--front .release-title{left:228px;top:172px;font-size:11px}

  .tracklist{position:absolute;left:24px;top:26px;list-style:none;color:var(--ink-soft);text-transform:uppercase}
  .tracklist li{font-size:17px;font-weight:700;letter-spacing:1.5px;line-height:22.5px;display:flex;gap:10px;align-items:baseline}
  .tracklist__no{font-size:11px;width:12px}

  .credits{position:absolute;left:0;right:0;bottom:14px;text-align:center;font-family:"Oswald",sans-serif;font-weight:500;font-size:6.2px;color:var(--ink);line-height:17px;text-transform:uppercase}

  .lyrics{position:absolute;left:50px;top:224px;width:250px;text-align:center;font-weight:800;font-size:12.5px;line-height:14px;color:rgba(42,42,46,.85);text-transform:uppercase;letter-spacing:.3px}

  .disc{position:absolute;left:753px;top:279px;width:300px;height:300px}
</style>
</head>
<body>

  <section class="panel panel--front" aria-label="Front cover">
    <div class="artwork" role="img" aria-label="Faceted ink clouds in peach, pink and violet drifting across white"></div>
    <div class="brand"><span class="brand__square"></span><span class="brand__name">OKAPIMIND</span></div>
    <p class="release-title">Open Gates</p>
  </section>

  <section class="panel panel--back" aria-label="Back cover">
    <div class="artwork" role="img" aria-label="Faceted ink cloud in violet, indigo and peach rising through the panel"></div>
    <ol class="tracklist">
      <li><span class="tracklist__no">1.</span>Velvet Spoon</li>
      <li><span class="tracklist__no">2.</span>Hold It Near</li>
      <li><span class="tracklist__no">3.</span>Harbor Pike</li>
      <li><span class="tracklist__no">4.</span>Can We Stay</li>
      <li><span class="tracklist__no">5.</span>Brightest Edge</li>
    </ol>
    <div class="credits">
      <p>Recording by Mustermann | Mix by Musterfrau | Mastering by Mustermännchen</p>
      <p>Recording by Mustermann | Mix by Musterfrau | Mastering by Mustermännchen</p>
    </div>
  </section>

  <svg class="disc" viewBox="0 0 300 300" aria-label="Disc label">
    <defs>
      <clipPath id="disc-face"><circle cx="150" cy="150" r="146"/></clipPath>
      <radialGradient id="ink-peach" cx="50%" cy="50%" r="50%"><stop offset="0" stop-color="#f4cdb0"/><stop offset="1" stop-color="#f4cdb0" stop-opacity="0"/></radialGradient>
      <radialGradient id="ink-violet" cx="50%" cy="50%" r="50%"><stop offset="0" stop-color="#6b3fa8" stop-opacity=".85"/><stop offset="1" stop-color="#6b3fa8" stop-opacity="0"/></radialGradient>
      <radialGradient id="ink-magenta" cx="50%" cy="50%" r="50%"><stop offset="0" stop-color="#b6338f" stop-opacity=".8"/><stop offset="1" stop-color="#b6338f" stop-opacity="0"/></radialGradient>
      <path id="disc-rim" d="M22.5,184.2 A132,132 0 1 0 274,104.9"/>
    </defs>
    <circle cx="150" cy="150" r="147" fill="#fff" stroke="#cfcfd2" stroke-width="1.5"/>
    <g clip-path="url(#disc-face)" role="img" aria-label="Faceted ink clouds in peach, pink and violet">
      <ellipse cx="90" cy="40" rx="70" ry="45" fill="url(#ink-peach)"/>
      <ellipse cx="225" cy="55" rx="70" ry="50" fill="url(#ink-peach)"/>
      <ellipse cx="65" cy="150" rx="55" ry="55" fill="url(#ink-violet)"/>
      <ellipse cx="215" cy="130" rx="45" ry="40" fill="url(#ink-magenta)"/>
      <ellipse cx="250" cy="200" rx="45" ry="40" fill="url(#ink-peach)"/>
      <ellipse cx="150" cy="95" rx="45" ry="30" fill="url(#ink-magenta)"/>
      <ellipse cx="110" cy="215" rx="40" ry="30" fill="url(#ink-magenta)"/>
    </g>
    <circle cx="150" cy="150" r="47" fill="#fff" opacity=".7"/>
    <circle cx="150" cy="150" r="38" fill="var(--stage)" stroke="#cfcfd2"/>
    <rect x="82" y="230" width="8" height="8" fill="#2a2a2e"/>
    <text x="93" y="238" font-family="Raleway, sans-serif" font-weight="300" font-size="20" fill="#2a2a2e">OKAPIMIND</text>
    <text x="163" y="250" font-family="Montserrat, sans-serif" font-weight="700" font-size="9" letter-spacing="1.2" fill="#c9c9cc">OPEN GATES</text>
    <text font-family="Montserrat, sans-serif" font-weight="700" font-size="6.5" letter-spacing=".6" fill="#444">
      <textPath href="#disc-rim" startOffset="2%">1. VELVET SPOON | 2. HOLD IT NEAR | 3. HARBOR PIKE | 4. CAN WE STAY | 5. BRIGHTEST EDGE</textPath>
    </text>
  </svg>

  <section class="panel panel--inside-left" aria-label="Inside left">
    <div class="artwork" role="img" aria-label="Faceted ink clouds in pink, peach and indigo spreading down the panel"></div>
    <p class="lyrics">Skin burned red<br>and scarfes and hats<br>open gates like ads on TV<br>like leaves in the wind</p>
  </section>

  <section class="panel panel--inside-right" aria-label="Inside right">
    <div class="artwork" role="img" aria-label="Faceted ink cloud in peach, violet and magenta along the right side"></div>
  </section>

</body>
</html>
```